physio rehab flyer for Vela Mend please

Specification:
Flyer is to be trifold from letter size (8.5 x 11)
-----------------------This may help you:--------------------------
I would like the look of :
clean, minimalistic look with mainly blue and green
san serif font
professional
The colors I like are blue (not the blue in the logo enclosed, I want a change, but more like the blue on my website logo) and light green.
This is my website: www.velamendgroup.ca just so you get an idea but it will be totally changed soon to a to be determined design.
I like the blue and green in file "sample 2" (enclosed)
I like the pictures in "sample 2" file enclosed
For inspiration, I like design of this brochure: http://www.brelford.ca/HarlowRehab/PatientsFamilies/Clinics_Tests/DKAP_Service/Documents/Brochure.pdf
Here's how I see the pages layout:
----[location: this should be the cover (outside, right panel of trifold)]-----
Vela Mend Logo
Integrated Injury Rehab
Evidence-based, one-on-one care to make your recovery fast and comfortable
www.velamendgroup.ca
---------------[location: inside, left panel]----------------------------------------
Our team leaders
[portrait here]
Harriet Olsavik, MD, FRCPC, MSC, CIME
Physiatrist
Dr. Olsavik specializes in injury rehab and sports medicine. She is highly trained having received her MD and Residency in Physiatry from Pellham Institute. Her passion is to help injured people get back to their life.
[portrait here]
Wendy Carstairs, PT
Physiotherapist
Wendy has over 10 years of experience as a Physiotherapist (5 in Canada). She has advanced training in orthopedics and manual therapy. She loves and relates well with people from the youngest to the most senior.
--------------------[location: inside, middle panel]-------------------------------
Our services
We provide integrated assessment and care from interprofessional team of regulated healthcare professionals with proven experience in injury rehabilitation:
physiatrists
sport medicine physicians
physiotherapists
chiropractors
massage therapists
acupuncturists
psychologists
We provide custom medical bracing, orthotics, orthopedic shoes, assistive devices, and medical stockings, all in one place.
----------------------[location: inside, right panel]-----------------------------------
Only registered physiotherapists
We strongly believe in consistency with your treatment plan. This means that you spend your time here one-on-one with your physiotherapist, not any students or assistants. You get consistent high quality care from a professional.
One-on-one attention
We book maximum 3 people per hour to ensure everyone gets adequate one-on-one time with their physiotherapist. This compares favorably with other clinics, who may book upwards of 5-6 per hour. The atmosphere is professional -balanced with friendly, caring and relaxed. Our highly qualified staff operate this way to help make your recovery faster and more enjoyable.
------------------------[location: outside, left panel]---------------------------------
The right rehab for your clients
Timely access to comprehensive assessment and treatment
Proven track record in injury rehabilitation
Convenient one-stop service
Customized treatment plans
Integrated, co-ordinated care
Evidence-based care applying leading best practices
Access to specialty clinics: Physiatry and Chronic Pain
-------------------------[location: outside, middle panel]--------------------------
Please call us 555-384-2096
for more information on injury rehabilitation
Vela Mend Group
1862 Wexmoor Rd., Unit 9
Scarborough, ON K4T 8B2
[Please include a line art map designed based on "map" file enclosed]
To make a referral for your clients, contact velamendgroup@corvamail.ca or fax: 555-384-2071. Thank you.
www.velamendgroup.ca
------------------------------------------------------------------------------------------------
Target Market(s)
family doctors, ER docs, lawyers, and general public age (20-50)
Industry/Entity Type
Health And Wellness
Requirements
Must have
- san serif font
- blue and green colors
- clean, sophisticated look
Nice to have
- consumer choice award badge either on front or back of trifold
- see above

```html
<!DOCTYPE html>
<html lang="en">
<head>
<meta charset="utf-8">
<title>Vela Mend — Integrated Injury Rehab</title>
<link rel="stylesheet" href="https://fonts.googleapis.com/css2?family=Ubuntu:ital,wght@0,300;0,400;0,500;1,400&display=swap">
<style>
  :root {
    --navy: #2c4f86;
    --navy-deep: #23447a;
    --lime: #8dc63f;
    --lime-text: #a9d14a;
    --sky: #7aa6dc;
    --paper: #efeff1;
    --ink-blue: #2c4f86;
    --on-navy: #e9eef6;
    --on-navy-soft: #d8e0ee;
  }
  html, body {
    margin: 0;
    padding: 0;
    overflow: hidden;
    background: #ffffff;
  }
  .spread {
    position: relative;
    width: 1200px;
    height: 929px;
    overflow: hidden;
    font-family: "Ubuntu", sans-serif;
    font-weight: 300;
  }
  .backdrop {
    position: absolute;
    inset: 0;
    width: 1200px;
    height: 929px;
  }
  .block { position: absolute; }
  .bio-name {
    text-align: right;
    font-size: 17px;
    line-height: 22px;
    color: var(--on-navy);
    font-weight: 400;
  }
  .bio-name .name { color: var(--lime-text); font-weight: 500; }
  .bio-name .role {
    display: block;
    font-style: italic;
    font-size: 14px;
    color: var(--lime-text);
    font-weight: 400;
  }
  .bio-name .role.light { color: var(--on-navy); }
  .copy {
    margin: 0;
    font-size: 15px;
    line-height: 22px;
    text-align: justify;
    color: var(--on-navy);
    letter-spacing: 0.2px;
  }
  .services-title {
    margin: 0;
    font-size: 29px;
    font-weight: 500;
    color: var(--ink-blue);
  }
  .services-copy {
    margin: 0;
    font-size: 15px;
    line-height: 22.5px;
    text-align: justify;
    color: var(--ink-blue);
    letter-spacing: 0.3px;
  }
  .service-list {
    list-style: none;
    margin: 0;
    padding: 0;
  }
  .service-list li {
    display: flex;
    align-items: center;
    height: 30px;
    font-size: 16px;
    font-weight: 500;
    color: var(--ink-blue);
  }
  .service-list svg { margin-right: 7px; flex: none; }
  .brand {
    text-align: center;
    color: #ffffff;
  }
  .brand-name {
    display: inline-flex;
    align-items: center;
    gap: 6px;
    font-size: 22px;
    font-weight: 500;
    line-height: 24px;
    color: #ffffff;
  }
  .brand-dot {
    width: 10px; height: 10px; border-radius: 50%;
    background: var(--lime);
  }
  .brand-tag {
    display: block;
    font-size: 8px;
    margin-top: 4px;
    border-top: 1px solid #ffffff;
    padding-top: 2px;
    width: 64px;
    margin-left: auto;
    margin-right: auto;
  }
  .feature-title {
    margin: 0;
    font-size: 23px;
    font-style: italic;
    font-weight: 400;
    color: var(--lime-text);
  }
</style>
</head>
<body>
<div class="spread">

  <svg class="backdrop" viewBox="0 0 1200 929" xmlns="http://www.w3.org/2000/svg">
    <defs>
      <linearGradient id="portrait-tone" x1="0" y1="0" x2="1" y2="1">
        <stop offset="0" stop-color="#b89a7a"/>
        <stop offset="0.55" stop-color="#e6e2dc"/>
        <stop offset="1" stop-color="#cfc9c2"/>
      </linearGradient>
      <linearGradient id="portrait-tone-two" x1="0" y1="0" x2="1" y2="1">
        <stop offset="0" stop-color="#c9d4dc"/>
        <stop offset="0.5" stop-color="#d7b7a2"/>
        <stop offset="1" stop-color="#b8a4b6"/>
      </linearGradient>
      <linearGradient id="brace-tone" x1="0" y1="0" x2="1" y2="1">
        <stop offset="0" stop-color="#f4f4f6"/>
        <stop offset="0.4" stop-color="#dcc2ae"/>
        <stop offset="0.7" stop-color="#a9c6e6"/>
        <stop offset="1" stop-color="#f4f4f6"/>
      </linearGradient>
      <linearGradient id="massage-tone" x1="0" y1="0" x2="1" y2="1">
        <stop offset="0" stop-color="#e8c7a9"/>
        <stop offset="0.5" stop-color="#d9a582"/>
        <stop offset="1" stop-color="#c88a62"/>
      </linearGradient>
    </defs>

    <!-- left panel -->
    <rect x="0" y="0" width="400" height="929" fill="var(--navy)"/>
    <rect x="0" y="0" width="25" height="929" fill="var(--lime)"/>

    <!-- middle panel -->
    <rect x="400" y="0" width="400" height="929" fill="var(--paper)"/>

    <!-- right panel -->
    <rect x="800" y="0" width="400" height="929" fill="var(--navy)"/>
    <rect x="1175" y="0" width="25" height="640" fill="var(--lime)"/>

    <!-- top portrait frame -->
    <path d="M0,55 Q0,35 30,35 L120,35 Q150,35 170,58 L230,135 Q250,162 230,190 L170,272 Q150,295 120,295 L0,295 Z" fill="#e4e6ea"/>
    <path d="M0,55 Q0,35 30,35 L120,35 Q150,35 170,58 L230,135 Q250,162 230,190 L170,272 Q150,295 120,295" fill="none" stroke="var(--lime)" stroke-width="2" transform="translate(18,-6)"/>
    <g role="img" aria-label="Portrait of Dr. Harriet Olsavik in a white coat in front of file shelves">
      <path d="M0,55 Q0,35 28,35 L95,35 Q122,35 140,56 L195,132 Q213,160 195,188 L140,272 Q122,295 95,295 L0,295 Z" fill="url(#portrait-tone)"/>
    </g>

    <!-- second portrait frame -->
    <path d="M0,485 Q0,465 30,465 L120,465 Q150,465 170,488 L230,565 Q250,592 230,620 L170,702 Q150,725 120,725 L0,725 Z" fill="#e4e6ea"/>
    <path d="M0,485 Q0,465 30,465 L120,465 Q150,465 170,488 L230,565 Q250,592 230,620 L170,702 Q150,725 120,725" fill="none" stroke="var(--lime)" stroke-width="2" transform="translate(18,-6)"/>
    <g role="img" aria-label="Portrait of physiotherapist Wendy Carstairs smiling">
      <path d="M0,485 Q0,465 28,465 L95,465 Q122,465 140,486 L195,562 Q213,590 195,618 L140,702 Q122,725 95,725 L0,725 Z" fill="url(#portrait-tone-two)"/>
    </g>

    <!-- middle top ribbon and photo -->
    <path d="M280,0 L330,0 C380,90 420,210 470,290 C510,340 570,352 640,346 C560,366 480,348 435,290 C380,210 330,90 280,0 Z" fill="var(--sky)"/>
    <g role="img" aria-label="Therapist fitting a knee brace on a patient's leg">
      <path d="M400,0 L800,0 L800,282 C730,322 640,342 560,338 C480,330 440,250 410,180 L400,150 Z" fill="url(#brace-tone)"/>
    </g>
    <path d="M400,170 C440,260 480,345 570,356 C650,364 740,330 800,286" fill="none" stroke="var(--navy)" stroke-width="1.5"/>
    <path d="M560,340 C650,340 730,320 800,282" fill="none" stroke="var(--lime)" stroke-width="2"/>

    <!-- right bottom photo -->
    <path d="M710,929 C790,800 840,660 920,590 C980,545 1070,580 1200,640" fill="none" stroke="#ffffff" stroke-width="2"/>
    <g role="img" aria-label="Hands massaging a patient's lower back">
      <path d="M730,929 C800,800 850,660 930,600 C985,565 1070,595 1200,650 L1200,929 Z" fill="url(#massage-tone)"/>
    </g>
    <path d="M890,620 C940,585 1000,585 1070,605 C1110,617 1150,632 1175,640" fill="none" stroke="var(--lime)" stroke-width="2.5"/>
  </svg>

  <!-- left panel: team leaders -->
  <div class="block bio-name" style="left:150px; top:234px; width:212px;">
    <span class="name">Harriet Olsavik,</span><br>MD, FRCPC, MSC, CIME
    <span class="role">Physiatrist</span>
  </div>
  <p class="block copy" style="left:60px; top:312px; width:302px;">Dr. Olsavik specializes in injury rehab and sports medicine. She is highly trained having received her MD and Residency in Physiatry from Pellham Institute. Her passion is to help injured people get back to their life.</p>

  <div class="block bio-name" style="left:150px; top:684px; width:212px;">
    <span class="name">Wendy Carstairs,</span> PT
    <span class="role light">Physiotherapist</span>
  </div>
  <p class="block copy" style="left:60px; top:739px; width:302px;">Wendy has over 10 years of experience as a Physiotherapist (5 in Canada). She has advanced training in orthopedics and manual therapy. She loves and relates well with people form the youngest to the most senior.</p>

  <!-- middle panel: services -->
  <h2 class="block services-title" style="left:461px; top:380px;">Our services</h2>
  <p class="block services-copy" style="left:461px; top:431px; width:296px;">We provide integrated assessment and care from interprofessional team of regulated healthcare professionals with proven experience in injury rehabilitation:</p>

  <ul class="block service-list" style="left:461px; top:541px;">
    <li><svg width="15" height="15" viewBox="0 0 15 15"><circle cx="7.5" cy="7.5" r="6.5" fill="none" stroke="var(--lime)" stroke-width="1.3"/><path d="M4,7.5 L6.8,10.2 L13,3" fill="none" stroke="var(--ink-blue)" stroke-width="1.6"/></svg>physiatrists</li>
    <li><svg width="15" height="15" viewBox="0 0 15 15"><circle cx="7.5" cy="7.5" r="6.5" fill="none" stroke="var(--lime)" stroke-width="1.3"/><path d="M4,7.5 L6.8,10.2 L13,3" fill="none" stroke="var(--ink-blue)" stroke-width="1.6"/></svg>sport medicine physicians</li>
    <li><svg width="15" height="15" viewBox="0 0 15 15"><circle cx="7.5" cy="7.5" r="6.5" fill="none" stroke="var(--lime)" stroke-width="1.3"/><path d="M4,7.5 L6.8,10.2 L13,3" fill="none" stroke="var(--ink-blue)" stroke-width="1.6"/></svg>physiotherapists</li>
    <li><svg width="15" height="15" viewBox="0 0 15 15"><circle cx="7.5" cy="7.5" r="6.5" fill="none" stroke="var(--lime)" stroke-width="1.3"/><path d="M4,7.5 L6.8,10.2 L13,3" fill="none" stroke="var(--ink-blue)" stroke-width="1.6"/></svg>chiropractors</li>
    <li><svg width="15" height="15" viewBox="0 0 15 15"><circle cx="7.5" cy="7.5" r="6.5" fill="none" stroke="var(--lime)" stroke-width="1.3"/><path d="M4,7.5 L6.8,10.2 L13,3" fill="none" stroke="var(--ink-blue)" stroke-width="1.6"/></svg>massage therapists</li>
    <li><svg width="15" height="15" viewBox="0 0 15 15"><circle cx="7.5" cy="7.5" r="6.5" fill="none" stroke="var(--lime)" stroke-width="1.3"/><path d="M4,7.5 L6.8,10.2 L13,3" fill="none" stroke="var(--ink-blue)" stroke-width="1.6"/></svg>acupuncturists</li>
    <li><svg width="15" height="15" viewBox="0 0 15 15"><circle cx="7.5" cy="7.5" r="6.5" fill="none" stroke="var(--lime)" stroke-width="1.3"/><path d="M4,7.5 L6.8,10.2 L13,3" fill="none" stroke="var(--ink-blue)" stroke-width="1.6"/></svg>psychologists</li>
  </ul>

  <p class="block services-copy" style="left:461px; top:782px; width:296px;">We provide custom medical bracing, orthotics, orthopedic shoes, assistive devices, and medical stockings, all in one place.</p>

  <!-- right panel: brand and features -->
  <div class="block brand" style="left:920px; top:30px; width:150px;">
    <span class="brand-name">Vela Mend<span class="brand-dot"></span></span>
    <span class="brand-tag">Integrated Injury Rehab</span>
  </div>

  <h3 class="block feature-title" style="left:843px; top:108px;">Only registered physiotherapists</h3>
  <p class="block copy" style="left:843px; top:146px; width:294px;">We strongly believe in consistency with your treatment plan. This means that you spend your time here one-on-one with your physiotherapist, not any students or assistants. You get consistent high quality care from a professional.</p>

  <h3 class="block feature-title" style="left:843px; top:318px;">One-on-one attention</h3>
  <p class="block copy" style="left:843px; top:355px; width:294px;">We book maximum 3 people per hour to ensure everyone gets adequate one-on-one time with their physiotherapist. This compares favorably with other clinics, who may book upwards of 5-6 per hour. The atmosphere is professional -balanced with friendly, caring and relaxed. Our highly qualified staff operate this way to help make your recovery faster and more enjoyable.</p>

</div>
</body>
</html>
```